Construction Directory Website Flyer

We need a postcard size +/- or somewhere around that size (something standard) flyer designed for our construction directory website. Leave a spot for tagline. Call to action is 'register your company now'. I am thinking many mini pictures of different construction to show that it is for the entire construction industry. Logo and screenshot of the homepage of the website is attached. Use same theme as webpage.

Target Market(s)

Construction Industry

Industry/Entity Type

Construction

Font styles to use
Sans Serif

Requirements
Must have
• Call to action
• Colors to match logo
• Area to add description and details.
Nice to have
• Construction Images
Should not have
• No Cartoonish types of things

```html
<!DOCTYPE html>
<html lang="en">
<head>
<meta charset="utf-8">
<title>Built By Construction For Construction – Flyer</title>
<link href="https://fonts.googleapis.com/css2?family=Oswald:wght@200;300;400;700&family=Roboto+Condensed:wght@400;700&family=Montserrat:wght@500&display=swap" rel="stylesheet">
<style>
  :root {
    --orange: #e05a1b;
    --red: #d9261c;
    --slate: #3d434b;
    --grey-bar: #c4c4c4;
    --paper: #ffffff;
    --backdrop: #e6e6e6;
  }
  html, body {
    margin: 0;
    width: 1200px;
    height: 1200px;
    overflow: hidden;
    background: var(--backdrop);
  }
  .flyer {
    position: absolute;
    left: 170px;
    top: 45px;
    width: 860px;
    height: 1110px;
    background: var(--paper);
    overflow: hidden;
    box-shadow: 0 6px 24px rgba(0,0,0,.18);
  }
  .headline {
    position: absolute;
    left: 48px;
    top: 28px;
    margin: 0;
    font-family: 'Oswald', sans-serif;
    font-weight: 200;
    line-height: 1;
  }
  .headline-top {
    display: block;
    color: var(--red);
    font-size: 78px;
    letter-spacing: 1px;
  }
  .headline-bottom {
    display: block;
    margin-top: 10px;
    color: var(--slate);
    font-size: 60px;
    font-weight: 300;
    letter-spacing: -1px;
  }
  .headline-bottom strong {
    color: var(--red);
    font-weight: 700;
  }
  .headline-rule {
    position: absolute;
    left: 300px;
    top: 104px;
    width: 480px;
    height: 2px;
    background: var(--slate);
  }
  .collage {
    position: absolute;
    left: 0;
    top: 0;
    width: 860px;
    height: 1110px;
  }
  .cta {
    position: absolute;
    left: 40px;
    top: 912px;
    font-family: 'Roboto Condensed', sans-serif;
    transform: rotate(-3deg);
    transform-origin: left top;
  }
  .cta-title {
    display: block;
    font-family: 'Oswald', sans-serif;
    font-weight: 700;
    font-size: 62px;
    line-height: 1;
    color: var(--orange);
  }
  .cta-sub {
    display: block;
    font-size: 32px;
    line-height: 1.15;
    color: var(--slate);
    margin-top: 2px;
  }
  .cta-url {
    display: inline-block;
    margin-top: 12px;
    padding: 5px 34px 5px 12px;
    background: var(--slate);
    color: #fff;
    font-size: 26px;
    line-height: 1.2;
    position: relative;
  }
  .cta-url::after {
    content: "";
    position: absolute;
    right: -26px;
    top: 0;
    width: 12px;
    height: 100%;
    background: var(--orange);
    transform: skewX(38deg);
  }
  .brand {
    position: absolute;
    left: 430px;
    top: 950px;
    display: flex;
    align-items: center;
    gap: 14px;
    transform: rotate(-3deg);
  }
  .brand-mark {
    width: 52px;
    height: 52px;
    background: var(--orange);
  }
  .brand-divider {
    width: 2px;
    height: 80px;
    background: var(--slate);
  }
  .brand-name {
    font-family: 'Montserrat', sans-serif;
    font-weight: 500;
    font-size: 29px;
    color: var(--slate);
  }
  .footer-band {
    position: absolute;
    left: 0;
    bottom: 0;
    width: 100%;
    height: 22px;
    background: var(--slate);
  }
</style>
</head>
<body>
  <main class="flyer">
    <svg class="collage" viewBox="0 0 860 1110" xmlns="http://www.w3.org/2000/svg">
      <defs>
        <linearGradient id="crane-tone" x1="0" y1="0" x2="0" y2="1">
          <stop offset="0" stop-color="#f08a5a"/>
          <stop offset="1" stop-color="#b8421a"/>
        </linearGradient>
        <linearGradient id="desk-tone" x1="0" y1="0" x2="1" y2="1">
          <stop offset="0" stop-color="#7a5a3a"/>
          <stop offset="1" stop-color="#d8d2c8"/>
        </linearGradient>
        <linearGradient id="site-tone" x1="0" y1="0" x2="0" y2="1">
          <stop offset="0" stop-color="#5d8cc4"/>
          <stop offset="1" stop-color="#b8c93a"/>
        </linearGradient>
        <linearGradient id="plans-tone" x1="0" y1="0" x2="1" y2="0">
          <stop offset="0" stop-color="#c9a57a"/>
          <stop offset="1" stop-color="#e9e4dc"/>
        </linearGradient>
        <linearGradient id="house-tone" x1="0" y1="0" x2="1" y2="1">
          <stop offset="0" stop-color="#ececec"/>
          <stop offset="1" stop-color="#8a8d92"/>
        </linearGradient>
        <linearGradient id="worker-tone" x1="0" y1="0" x2="0" y2="1">
          <stop offset="0" stop-color="#a9bccb"/>
          <stop offset="1" stop-color="#6b6a68"/>
        </linearGradient>
      </defs>

      <g class="crane-photo" role="img" aria-label="Tower crane silhouetted against an orange sky">
        <polygon points="0,255 245,255 110,810 0,810" fill="url(#crane-tone)"/>
      </g>

      <polygon class="accent-band" points="228,395 860,385 860,690 142,735" fill="var(--orange)"/>
      <polygon class="grey-bar" points="340,255 402,255 232,830 170,830" fill="var(--grey-bar)"/>
      <polygon class="grey-bar" points="610,368 662,368 565,800 512,800" fill="var(--grey-bar)"/>
      <polygon class="accent-corner" points="860,800 860,1088 835,1088 818,820" fill="var(--orange)"/>

      <g class="desk-photo" role="img" aria-label="Desk with hard hat, blueprints and tools">
        <polygon points="505,205 800,205 790,370 475,370" fill="url(#desk-tone)"/>
      </g>
      <g class="site-photo" role="img" aria-label="Workers in hard hats and hi-vis vests surveying a building site">
        <polygon points="372,415 592,415 552,710 302,710" fill="url(#site-tone)"/>
      </g>
      <g class="plans-photo" role="img" aria-label="Two builders in hard hats reviewing plans">
        <polygon points="650,415 835,415 805,690 605,690" fill="url(#plans-tone)"/>
      </g>
      <g class="house-photo" role="img" aria-label="House model and hard hat on architectural drawings">
        <polygon points="312,720 540,720 510,895 282,895" fill="url(#house-tone)"/>
      </g>
      <g class="worker-photo" role="img" aria-label="Worker cutting concrete with a power saw">
        <polygon points="632,700 810,700 790,915 598,915" fill="url(#worker-tone)"/>
      </g>
    </svg>

    <h1 class="headline">
      <span class="headline-top">BUILT BY</span>
      <span class="headline-bottom">CONSTRUCTION FOR <strong>CONSTRUCTION</strong></span>
    </h1>
    <div class="headline-rule"></div>

    <section class="cta">
      <span class="cta-title">REGISTER</span>
      <span class="cta-sub">your company now!</span>
      <span class="cta-url">www.buildlinked-site.com</span>
    </section>

    <div class="brand">
      <div class="brand-mark"></div>
      <div class="brand-divider"></div>
      <div class="brand-name">BuildLinked.com</div>
    </div>

    <div class="footer-band"></div>
  </main>
</body>
</html>
```